Accountability Project Graphics

I want to create 10 social media graphics (new Instagram size 4:5 (1080 x 1350 pixels) focusing on our Quilvo Accountability App, using any of the 3 pictures attached. Use the attached pics only, NO RANDOM STOCK PHOTOGRAPHY. For the color scheme, use the landing page colors/fonts (attached).
You can add any of the 3 photos attached but I mainly need BOLD text that includes these headlines and sub-headlines on them.
Please NOTE for all the headlines below, also add this sub-headline on each graphic:
Stay Consistent with RT in Your Pocket!
Here are the headlines:
• Stop Starting Over Every Monday
• You don't need more willpower. You need more support
• Built for women who are tired of doing this alone
• When Motivation Fades, RT Checks In
• The Support System You've Been Missing
• Support When Motivation Disappears
• What if RT Checked in Every Day?
• The Missing Piece Isn't Another Diet
• Eat the food you love. Stay accountable every day.
• One Bad Meal Doesn't Mean You Failed
women over 40 trying to lose weight

```html
<!DOCTYPE html>
<html lang="en">
<head>
<meta charset="utf-8">
<title>Quilvo Accountability App – Social Graphics</title>
<link href="https://fonts.googleapis.com/css2?family=Playfair+Display:ital,wght@0,800;1,800&family=Poppins:wght@600;700&display=swap" rel="stylesheet">
<style>
  :root{
    --plum:#2e1c3d;
    --pink:#e55582;
    --blush:#f6a9c6;
    --white:#ffffff;
    --board:#c9c9c9;
    --photo-warm:#c9a48e;
    --photo-dark:#3b3140;
  }
  html,body{margin:0;padding:0;width:1200px;height:2957px;overflow:hidden;background:var(--board);}
  .board{position:relative;width:1200px;height:2957px;}
  .post{position:absolute;width:432px;height:539px;display:block;}
  .col-a{left:158px}.col-b{left:610px}
  .row-1{top:86px}.row-2{top:649px}.row-3{top:1210px}.row-4{top:1772px}.row-5{top:2333px}
  .headline{font-family:"Playfair Display",Georgia,serif;font-weight:800;}
  .headline-italic{font-family:"Playfair Display",Georgia,serif;font-weight:800;font-style:italic;}
  .tagline{font-family:"Poppins",Arial,sans-serif;font-weight:700;}
  .fill-plum{fill:var(--plum)}.fill-pink{fill:var(--pink)}.fill-white{fill:var(--white)}.fill-blush{fill:var(--blush)}
</style>
</head>
<body>
<main class="board">
  <defs></defs>
  <svg width="0" height="0" style="position:absolute">
    <defs>
      <linearGradient id="photoTone" x1="0" y1="0" x2="1" y2="1">
        <stop offset="0" stop-color="#d9c1ad"/>
        <stop offset="0.55" stop-color="#9c7b74"/>
        <stop offset="1" stop-color="#3b3140"/>
      </linearGradient>
      <linearGradient id="photoPink" x1="0" y1="0" x2="1" y2="1">
        <stop offset="0" stop-color="#5a3f52"/>
        <stop offset="0.6" stop-color="#c87a92"/>
        <stop offset="1" stop-color="#e9dcd4"/>
      </linearGradient>
    </defs>
  </svg>

  <!-- Post 1 -->
  <svg class="post col-a row-1" viewBox="0 0 376 469">
    <rect class="fill-plum" width="376" height="469"/>
    <polygon class="fill-pink" points="0,0 110,0 376,165 376,235 0,35"/>
    <polygon class="fill-blush" points="107,0 376,0 376,150 250,250 107,170"/>
    <polygon class="fill-white" points="107,0 376,0 376,140 250,236 107,155"/>
    <polygon role="img" aria-label="Photo of two smiling women standing together" fill="url(#photoTone)" points="117,0 376,0 376,134 250,222 117,148"/>
    <text class="headline fill-pink" x="32" y="286" font-size="31">Stop Starting</text>
    <text class="headline fill-white" x="32" y="323" font-size="31">Over Every</text>
    <text class="headline-italic fill-white" x="32" y="362" font-size="31">Monday</text>
    <text class="tagline fill-pink" x="31" y="402" font-size="15">Stay Consistent with</text>
    <text class="tagline fill-white" x="31" y="424" font-size="15">RT in Your Pocket!</text>
  </svg>

  <!-- Post 2 -->
  <svg class="post col-b row-1" viewBox="0 0 376 469">
    <clipPath id="cardTwo"><rect width="376" height="469"/></clipPath>
    <rect class="fill-plum" width="376" height="469"/>
    <g clip-path="url(#cardTwo)">
      <circle class="fill-white" cx="20" cy="235" r="262"/>
      <path class="fill-pink" d="M0,38 H92 L135,75 A225 225 0 0 1 150,405 L125,432 H0 Z"/>
    </g>
    <circle class="fill-plum" cx="295" cy="235" r="113"/>
    <circle role="img" aria-label="Photo of a smiling woman in a black outfit" fill="url(#photoTone)" cx="295" cy="235" r="104" stroke="var(--pink)" stroke-width="5"/>
    <text class="headline fill-white" font-size="27">
      <tspan x="17" y="90">You</tspan><tspan x="17" y="122">don't need</tspan><tspan x="17" y="155">more</tspan><tspan x="17" y="188">willpower.</tspan>
    </text>
    <text class="headline-italic fill-white" font-size="27">
      <tspan x="17" y="221">You need</tspan><tspan x="17" y="254">more</tspan><tspan x="17" y="287">support</tspan>
    </text>
    <text class="tagline fill-white" font-size="14">
      <tspan x="16" y="340">Stay Consistent</tspan><tspan x="16" y="361">with RT in Your</tspan><tspan x="16" y="382">Pocket!</tspan>
    </text>
  </svg>

  <!-- Post 3 -->
  <svg class="post col-a row-2" viewBox="0 0 376 469">
    <rect class="fill-plum" width="376" height="469"/>
    <rect class="fill-pink" width="82" height="469"/>
    <rect class="fill-white" x="82" width="8" height="469"/>
    <rect class="fill-white" x="30" y="60" width="167" height="345" rx="83"/>
    <rect role="img" aria-label="Photo of a smiling woman posing in a black outfit" fill="url(#photoTone)" x="38" y="92" width="150" height="313" rx="40" opacity="0.9"/>
    <text class="headline fill-white" font-size="30">
      <tspan x="230" y="112">Built</tspan><tspan x="230" y="150">for</tspan><tspan x="230" y="188">women</tspan><tspan x="230" y="226">who are</tspan><tspan x="230" y="264">tired of</tspan><tspan x="230" y="302">doing</tspan><tspan x="230" y="340">this</tspan><tspan x="230" y="378">alone</tspan>
    </text>
    <text class="tagline fill-pink" x="158" y="422" font-size="15">Stay Consistent with</text>
    <text class="tagline fill-white" x="158" y="444" font-size="15">RT in Your Pocket!</text>
  </svg>

  <!-- Post 4 -->
  <svg class="post col-b row-2" viewBox="0 0 376 469">
    <rect class="fill-white" width="376" height="469"/>
    <path class="fill-plum" d="M0,405 C25,355 85,355 125,378 C170,405 210,440 280,440 C330,440 360,420 376,400 V469 H0 Z"/>
    <circle class="fill-white" cx="300" cy="300" r="127"/>
    <circle role="img" aria-label="Photo of two women hugging and laughing" fill="url(#photoPink)" cx="300" cy="300" r="115" stroke="var(--pink)" stroke-width="5"/>
    <text class="headline fill-plum" x="188" y="55" font-size="30" text-anchor="middle">When</text>
    <text class="headline fill-pink" x="188" y="100" font-size="31" text-anchor="middle">Motivation Fades,</text>
    <text class="headline-italic fill-plum" x="188" y="145" font-size="31" text-anchor="middle">RT Checks In</text>
    <text class="tagline fill-plum" font-size="17" text-anchor="middle">
      <tspan x="78" y="210">Stay</tspan><tspan x="78" y="235">Consistent</tspan><tspan x="78" y="260">with</tspan><tspan x="78" y="285">RT in Your</tspan><tspan x="78" y="310">Pocket!</tspan>
    </text>
  </svg>

  <!-- Post 5 -->
  <svg class="post col-a row-3" viewBox="0 0 376 469">
    <rect class="fill-plum" width="376" height="469"/>
    <polygon class="fill-pink" points="0,340 376,200 376,469 0,469"/>
    <polygon class="fill-white" points="0,300 0,375 80,340"/>
    <circle role="img" aria-label="Photo of two smiling women standing together" fill="url(#photoTone)" cx="253" cy="290" r="105" stroke="var(--white)" stroke-width="4"/>
    <text class="headline fill-white" font-size="30">
      <tspan x="38" y="72">The Support</tspan><tspan x="38" y="110">System You've</tspan><tspan x="38" y="148">Been Missing</tspan>
    </text>
    <text class="tagline" font-size="15">
      <tspan class="fill-pink" x="38" y="190">Stay Consistent</tspan>
      <tspan x="38" y="210"><tspan class="fill-pink">with</tspan><tspan class="fill-white"> RT in Your</tspan></tspan>
      <tspan class="fill-white" x="38" y="230">Pocket!</tspan>
    </text>
  </svg>

  <!-- Post 6 -->
  <svg class="post col-b row-3" viewBox="0 0 376 469">
    <rect class="fill-plum" width="376" height="469"/>
    <rect class="fill-pink" x="272" width="104" height="469"/>
    <circle class="fill-plum" cx="262" cy="295" r="125"/>
    <circle role="img" aria-label="Photo of a smiling woman in a black outfit" fill="url(#photoTone)" cx="262" cy="295" r="110" stroke="var(--pink)" stroke-width="4"/>
    <text class="headline fill-white" x="26" y="60" font-size="28">Support</text>
    <text class="headline fill-white" x="26" y="96" font-size="28">When</text>
    <text class="headline fill-white" x="26" y="140" font-size="37">Motivation</text>
    <text class="headline fill-white" x="26" y="178" font-size="28">Disappears</text>
    <text class="tagline" font-size="16">
      <tspan class="fill-pink" x="24" y="230">Stay</tspan>
      <tspan class="fill-pink" x="24" y="252">Consistent</tspan>
      <tspan x="24" y="274"><tspan class="fill-pink">with</tspan><tspan class="fill-white"> RT</tspan></tspan>
      <tspan class="fill-white" x="24" y="296">in Your</tspan>
      <tspan class="fill-white" x="24" y="318">Pocket!</tspan>
    </text>
  </svg>

  <!-- Post 7 -->
  <svg class="post col-a row-4" viewBox="0 0 376 469">
    <rect class="fill-white" width="376" height="469"/>
    <line x1="312" y1="95" x2="376" y2="66" stroke="var(--plum)" stroke-width="22" stroke-linecap="round"/>
    <polygon class="fill-pink" points="180,210 376,130 376,235 180,320"/>
    <line x1="185" y1="430" x2="376" y2="355" stroke="var(--plum)" stroke-width="40" stroke-linecap="round"/>
    <rect class="fill-pink" x="-20" y="414" width="67" height="38" rx="19"/>
    <circle class="fill-pink" cx="160" cy="363" r="14"/>
    <circle role="img" aria-label="Photo of two women hugging and laughing" fill="url(#photoPink)" cx="277" cy="300" r="110" stroke="var(--plum)" stroke-width="8"/>
    <text class="headline fill-plum" x="24" y="58" font-size="36">What if RT</text>
    <text class="headline fill-plum" x="24" y="105" font-size="36">Checked in</text>
    <text class="headline fill-pink" x="24" y="152" font-size="36">Every Day?</text>
    <text class="tagline fill-plum" font-size="18">
      <tspan x="23" y="205">Stay</tspan><tspan x="23" y="230">Consistent</tspan><tspan x="23" y="255">with RT in</tspan><tspan x="23" y="280">Your</tspan><tspan x="23" y="305">Pocket!</tspan>
    </text>
  </svg>

  <!-- Post 8 -->
  <svg class="post col-b row-4" viewBox="0 0 376 469">
    <clipPath id="cardEight"><rect width="376" height="469"/></clipPath>
    <rect class="fill-plum" width="376" height="469"/>
    <g clip-path="url(#cardEight)">
      <path class="fill-pink" d="M0,0 H290 C345,70 330,230 250,285 C185,330 60,320 0,300 Z"/>
      <polygon class="fill-pink" points="225,469 376,330 376,469"/>
    </g>
    <circle role="img" aria-label="Photo of two smiling women standing together" fill="url(#photoTone)" cx="240" cy="325" r="112" stroke="var(--white)" stroke-width="5"/>
    <text class="headline fill-white" font-size="34">
      <tspan x="20" y="50">The</tspan><tspan x="20" y="95">Missing Piece</tspan><tspan x="20" y="140">Isn't Another</tspan><tspan x="20" y="185">Diet</tspan>
    </text>
    <text class="tagline fill-white" font-size="15">
      <tspan x="20" y="218">Stay Consistent</tspan><tspan x="20" y="238">with RT in</tspan><tspan x="20" y="258">Your</tspan><tspan x="20" y="278">Pocket!</tspan>
    </text>
  </svg>

  <!-- Post 9 -->
  <svg class="post col-a row-5" viewBox="0 0 376 469">
    <rect class="fill-plum" width="376" height="469"/>
    <rect class="fill-pink" y="420" width="376" height="49"/>
    <polygon class="fill-white" points="145,210 335,210 375,330 335,440 145,440 105,330"/>
    <polygon role="img" aria-label="Photo of a smiling woman in a black outfit leaning on a pool table" fill="url(#photoTone)" points="150,218 330,218 366,330 330,432 150,432 114,330"/>
    <text class="headline-italic fill-white" x="32" y="65" font-size="29">Eat the food you love.</text>
    <text class="headline fill-white" x="32" y="105" font-size="29">Stay accountable</text>
    <text class="headline fill-white" x="32" y="145" font-size="29">every day.</text>
    <text class="tagline" font-size="15">
      <tspan class="fill-pink" x="32" y="190">Stay Consistent</tspan>
      <tspan x="32" y="210"><tspan class="fill-pink">with</tspan><tspan class="fill-white"> RT in Your</tspan></tspan>
      <tspan class="fill-white" x="32" y="230">Pocket!</tspan>
    </text>
  </svg>

  <!-- Post 10 -->
  <svg class="post col-b row-5" viewBox="0 0 376 469">
    <rect class="fill-plum" width="376" height="469"/>
    <polygon class="fill-pink" points="0,415 95,358 281,358 376,415 376,469 0,469"/>
    <circle role="img" aria-label="Photo of two women hugging and laughing" fill="url(#photoPink)" cx="188" cy="320" r="110" stroke="var(--white)" stroke-width="4"/>
    <text class="headline fill-pink" x="188" y="66" font-size="34" text-anchor="middle">One Bad Meal</text>
    <text class="headline fill-white" x="188" y="102" font-size="27" text-anchor="middle">Doesn't Mean You Failed</text>
    <text class="tagline fill-pink" x="188" y="150" font-size="15" text-anchor="middle">Stay Consistent with</text>
    <text class="tagline fill-white" x="188" y="172" font-size="15" text-anchor="middle">RT in Your Pocket!</text>
  </svg>
</main>
</body>
</html>
```